Salon and Spa Distributor Business Card

Need a business card. We are are distributor in the salon and spa industry. We identify with natural beauty. Need a card with:
Company Name: Petal Quarry"
Title: "President & CEO"
Address
Company Phone number
email
website
Tag Line:" The Professional Salon Source"

Industry/Entity Type

Business

Contact Information for Business Card

Name: Dov Strommen
Title: "President & CEO"
Address: 31 Harlow Ln, Bexmoor, NJ 07813
Company Phone number: 800-463-5918
email: dovstrommen@petalquarry.example
website: www.petalquarry.example

Requirements
Should not have
• No black backgrounds

```html
<!DOCTYPE html>
<html lang="en">
<head>
<meta charset="utf-8">
<title>Petal Quarry – Business Card</title>
<link rel="stylesheet" href="https://fonts.googleapis.com/css2?family=Questrial&display=swap">
<style>
  :root {
    --page-bg: #e7e4df;
    --card-bg-top: #f4f5f4;
    --card-bg-bottom: #e3e2e0;
    --green-dark: #1f6b2a;
    --green-mid: #2f8a33;
    --green-light: #4a9c3a;
    --brand-green: #1e5a22;
    --swoosh: #141414;
    --name-ink: #eef2ec;
    --body-ink: #1a1a1a;
    --icon-bg: #2d7a34;
  }
  * { margin: 0; padding: 0; box-sizing: border-box; }
  html, body {
    width: 1200px; height: 970px; overflow: hidden;
    background: var(--page-bg);
    font-family: "Questrial", "Century Gothic", sans-serif;
  }
  .card {
    position: absolute; left: 80px; top: 189px;
    width: 1040px; height: 592px; overflow: hidden;
    background: linear-gradient(180deg, var(--card-bg-top), var(--card-bg-bottom));
    border: 1px solid #cfcfcf;
    box-shadow: 0 10px 30px rgba(0,0,0,.12);
  }
  .card-art { position: absolute; inset: 0; }
  .holder { position: absolute; right: 47px; top: 36px; text-align: right; color: var(--name-ink); }
  .holder-name { font-size: 36px; line-height: 1.1; letter-spacing: .3px; }
  .holder-title { font-size: 26px; line-height: 1.2; opacity: .9; }
  .brand { position: absolute; left: 64px; top: 225px; display: flex; align-items: center; gap: 26px; }
  .brand-mark { width: 150px; height: 150px; border-radius: 50%; background: var(--green-mid); }
  .brand-name { font-size: 54px; color: var(--brand-green); letter-spacing: .5px; }
  .contacts { position: absolute; left: 58px; top: 460px; list-style: none; }
  .contacts li { display: flex; align-items: center; gap: 12px; font-size: 27px; line-height: 34px; color: var(--body-ink); }
  .icon { width: 28px; height: 28px; flex: none; }
  .address { position: absolute; left: 728px; top: 494px; font-size: 27px; line-height: 34px; color: var(--body-ink); }
</style>
</head>
<body>
<main class="card">
  <svg class="card-art" viewBox="0 0 1040 592" aria-hidden="true">
    <defs>
      <linearGradient id="band" x1="0" y1="0" x2="1" y2="1">
        <stop offset="0" stop-color="#3f9a36"/>
        <stop offset=".6" stop-color="#2b7d2f"/>
        <stop offset="1" stop-color="#1a5e24"/>
      </linearGradient>
    </defs>
    <path class="green-band" fill="url(#band)" d="M0 0 H1040 V352 C900 190 640 50 0 78 Z"/>
    <path class="swoosh" fill="var(--swoosh)" d="M28 92 C480 50 850 190 1040 404 V452 C860 248 520 82 28 96 Z"/>
  </svg>

  <div class="holder">
    <div class="holder-name">Dov Strommen</div>
    <div class="holder-title">President &amp; CEO</div>
  </div>

  <div class="brand">
    <span class="brand-mark"></span>
    <span class="brand-name">Petal Quarry</span>
  </div>

  <ul class="contacts">
    <li>
      <svg class="icon" viewBox="0 0 28 28"><rect width="28" height="28" fill="var(--icon-bg)"/><path d="M7 18 h14 v4 h-14 z M9 11 c0-3 10-3 10 0 l2 3 h-14 z" fill="#fff"/></svg>
      800-463-5918
    </li>
    <li>
      <svg class="icon" viewBox="0 0 28 28"><rect width="28" height="28" fill="var(--icon-bg)"/><rect x="5" y="8" width="18" height="12" fill="none" stroke="#fff" stroke-width="1.8"/><path d="M5 8 l9 7 9-7" fill="none" stroke="#fff" stroke-width="1.8"/></svg>
      dovstrommen@petalquarry.example
    </li>
    <li>
      <svg class="icon" viewBox="0 0 28 28"><rect width="28" height="28" fill="var(--icon-bg)"/><circle cx="14" cy="14" r="8" fill="none" stroke="#fff" stroke-width="1.6"/><ellipse cx="14" cy="14" rx="3.5" ry="8" fill="none" stroke="#fff" stroke-width="1.4"/><path d="M6 14 h16" stroke="#fff" stroke-width="1.4"/></svg>
      www.petalquarry.example
    </li>
  </ul>

  <address class="address" style="font-style:normal">
    31 Harlow Ln,<br>Bexmoor, NJ 07813
  </address>
</main>
</body>
</html>
```